New Bicycle shop business card

Hi!
I'm looking for a business card for my new proffesional bike mechanics shop. This shop is only for fixing broken bikes and not selling bikes.
Peferbly a modern and sleek and modern design.
Colors: black, grey, red, white
Information:
Name: Rijwielwerkplaats Vanhoutte
Shop owner: Bart Vanhoutte & Marieke Segers
Website: www.rijwielwerkplaats-vanhoutte.be
Email: info@rijwielwerkplaats-vanhoutte.be
Phone number: +32471902368
Street adres: Kerkweg 46
9940 Bellebeke
Slogan/shop information: Herstellingen van alle merken.
Logo: see files.
Target Market(s)
People who seek a mechanic to fix or upgrade their bikes.
Contact Information for Business Card
Information:
Website: info@rijwielwerkplaats-vanhoutte.be
9940 Bellebeke
Logo: see files.

```html
<!DOCTYPE html>
<html lang="nl">
<head>
<meta charset="utf-8">
<title>Rijwielwerkplaats Vanhoutte – visitekaartje</title>
<link rel="stylesheet" href="https://fonts.googleapis.com/css2?family=Montserrat:wght@600;800&family=Roboto:wght@400;500&display=swap">
<style>
  :root {
    --red: #d42a3a;
    --black: #1b1b1b;
    --grey: #9a9da0;
    --white: #ffffff;
    --backdrop: #d9d9d9;
    --muted-white: rgba(255,255,255,0.85);
  }
  * { box-sizing: border-box; margin: 0; padding: 0; }
  html, body { width: 1200px; height: 852px; overflow: hidden; }
  body {
    background: var(--backdrop);
    font-family: "Roboto", Arial, sans-serif;
    position: relative;
  }
  .card {
    position: absolute;
    left: 340px;
    width: 520px;
    height: 300px;
    border-radius: 22px;
    overflow: hidden;
    background: var(--white);
    box-shadow: 0 10px 24px rgba(0,0,0,0.18);
  }
  .card--front { top: 110px; }
  .card--back  { top: 442px; }

  /* Front */
  .wordmark {
    display: flex;
    align-items: center;
    justify-content: center;
    gap: 12px;
    margin-top: 82px;
  }
  .wordmark__square {
    width: 30px; height: 30px;
    background: var(--red);
    flex: none;
  }
  .wordmark__name {
    font-family: "Montserrat", Arial, sans-serif;
    font-weight: 800;
    color: var(--black);
    text-transform: uppercase;
    font-size: 22px;
    line-height: 1.1;
    letter-spacing: 1px;
  }
  .tagline {
    display: flex;
    align-items: center;
    justify-content: center;
    gap: 14px;
    margin-top: 40px;
    font-size: 13px;
    color: var(--black);
  }
  .tagline__rule { width: 36px; height: 2px; background: var(--red); }
  .edge-band {
    position: absolute;
    left: 0; right: 0; bottom: 0;
    height: 9px;
    display: flex;
  }
  .edge-band__red { width: 30%; background: var(--red); }
  .edge-band__grey { flex: 1; background: var(--grey); }

  /* Back */
  .back-shape { position: absolute; inset: 0; }
  .back-brand {
    position: absolute;
    left: 26px; top: 100px;
    width: 190px;
  }
  .back-brand .wordmark { margin-top: 0; justify-content: flex-start; gap: 10px; }
  .back-brand .wordmark__square { width: 22px; height: 22px; }
  .back-brand .wordmark__name { font-size: 15px; letter-spacing: 0.5px; }
  .back-brand .tagline { justify-content: flex-start; margin-top: 10px; font-size: 11px; }
  .contact {
    position: absolute;
    left: 282px; top: 58px;
    color: var(--white);
  }
  .contact__name {
    font-family: "Montserrat", Arial, sans-serif;
    font-weight: 800;
    font-size: 19px;
    text-transform: uppercase;
    letter-spacing: 1px;
  }
  .contact__role { font-size: 12px; color: var(--muted-white); margin-top: 2px; }
  .contact__list { list-style: none; margin-top: 22px; font-size: 12px; }
  .contact__list li { display: flex; align-items: center; gap: 9px; margin-bottom: 6px; }
  .contact__list svg { width: 12px; height: 12px; flex: none; fill: var(--white); }
  .contact__address { font-size: 12px; margin-top: 12px; line-height: 1.45; padding-left: 21px; }
</style>
</head>
<body>

<section class="card card--front" aria-label="Voorkant visitekaartje">
  <div class="wordmark">
    <span class="wordmark__square"></span>
    <span class="wordmark__name">Rijwielwerkplaats<br>Vanhoutte</span>
  </div>
  <p class="tagline">
    <span class="tagline__rule"></span>
    Herstellingen van alle merken
    <span class="tagline__rule"></span>
  </p>
  <div class="edge-band"><span class="edge-band__red"></span><span class="edge-band__grey"></span></div>
</section>

<section class="card card--back" aria-label="Achterkant visitekaartje">
  <svg class="back-shape" viewBox="0 0 520 300" preserveAspectRatio="none" aria-hidden="true">
    <path d="M230 0 C 268 80, 272 210, 232 300 L 520 300 L 520 0 Z" fill="var(--red)"/>
    <path d="M218 0 C 258 80, 262 210, 222 300" fill="none" stroke="var(--black)" stroke-width="6"/>
  </svg>

  <div class="back-brand">
    <div class="wordmark">
      <span class="wordmark__square"></span>
      <span class="wordmark__name">Rijwielwerkplaats<br>Vanhoutte</span>
    </div>
    <p class="tagline">Herstellingen van alle merken</p>
  </div>

  <div class="contact">
    <h1 class="contact__name">Marieke Segers</h1>
    <p class="contact__role">Owner</p>
    <ul class="contact__list">
      <li>
        <svg viewBox="0 0 24 24"><path d="M6.6 10.8a15 15 0 0 0 6.6 6.6l2.2-2.2a1 1 0 0 1 1-.25 11.4 11.4 0 0 0 3.6.57 1 1 0 0 1 1 1V20a1 1 0 0 1-1 1A17 17 0 0 1 3 4a1 1 0 0 1 1-1h3.5a1 1 0 0 1 1 1c0 1.25.2 2.45.57 3.57a1 1 0 0 1-.25 1z"/></svg>
        +32471902368
      </li>
      <li>
        <svg viewBox="0 0 24 24"><path d="M2 5h20v14H2z M4 7v.5l8 5 8-5V7l-8 5z" fill-rule="evenodd"/></svg>
        info@rijwielwerkplaats-vanhoutte.be
      </li>
      <li>
        <svg viewBox="0 0 24 24"><path d="M12 2a10 10 0 1 0 0 20 10 10 0 0 0 0-20zm6.9 6h-3a15 15 0 0 0-1.4-3.6A8 8 0 0 1 18.9 8zM12 4c.8 1.2 1.5 2.5 1.9 4h-3.8c.4-1.5 1.1-2.8 1.9-4zM4.3 14a8 8 0 0 1 0-4h3.4a16 16 0 0 0 0 4zm.8 2h3a15 15 0 0 0 1.4 3.6A8 8 0 0 1 5.1 16zm3-8h-3a8 8 0 0 1 4.4-3.6A15 15 0 0 0 8.1 8zM12 20c-.8-1.2-1.5-2.5-1.9-4h3.8c-.4 1.5-1.1 2.8-1.9 4zm2.3-6H9.7a14 14 0 0 1 0-4h4.6a14 14 0 0 1 0 4zm.2 5.6a15 15 0 0 0 1.4-3.6h3a8 8 0 0 1-4.4 3.6zm1.8-5.6a16 16 0 0 0 0-4h3.4a8 8 0 0 1 0 4z"/></svg>
        www.rijwielwerkplaats-vanhoutte.be
      </li>
    </ul>
    <p class="contact__address">Kerkweg 46<br>9940 Bellebeke</p>
  </div>
</section>

</body>
</html>
```